Hurricane Damage Public Adjuster Billboard

I have created several projects with you and have several great designs. I need to format them into a Billboard for upcoming Hurricane Season. Need done in a month. Im also in process of getting an eye catching and easy to remember 800# Vanity phone number like Call 800-Stormsafe or 800- Need Fix? My included past Craft Huddle projects will give you an idea of what colors, schemes, and designs I gravitate towards. 3 past Design projects were 1) 2 Logos where I picked the 1st place and the 2nd place and 2) Index Card where I picked the winner as the Index Card and the 2nd place as a Post Card. Point is, I will pick and pay for 2 winners if they're good. This should help to sweeten the pot. Also, please look at my website for ideas that I like:

www.TheClaimKeeperGroup.com
I want people to feel that I am the best and highest. Level.

I've been getting a lot of quick half effort designs basically cut & pasting my previous projects. Please don't rush and take your time to be creative. A an example, my Biggest Competitor is Vesta Public Adjusting. Their colors are Black and Gold while mine are Blue, White, and Black with a highlight of Orange if possible. I JUST imported a picture of their BillBoard. I need mine better and BLOW AWAY THEIRS. Terms like "Don't be Victimized Twice ?, Don't let the Hurricane Ruin your Life?". "Get Fairly Paid & Move On" "Our Clients Claims are VIP?
Updates

I'm getting a lot of quick half effort ones. I'd rather you take your time and really put some thoughts and effort into it. My Biggest Competitor is Vesta Public Adjusting. They have black & gold colors, while I have Blue, Black, and white.

It needs to blow theirs away. I have imported their Billboard for comparative purposes.

Guy's,
I'll make it easier for you in what I'm looking for. Please look at the Vesta Billboard picture attached.

1) Put my "Blue Shield" to the left, replacing their logo
2) change color patterns from their (Black, Gold, White) to my color schemes of (Black, Blue, White)
3) I want to see my name where their is:

THE
Claim Keeper's Group
EXPERT & LOCAL Public Adjusters
"FOR THE POLICYHOLDER!!"

4) to the right, add the A+Rated logo and QRS+ Accredited logo, 5 Star Zorbix Rated logo, 5 Start PORCHLINE Highly Rated logo, etc..

5) the right side is where you can be creative as I will not have a picture of me there.

"20+ Years of Experience, Recovering Millions for our VIP Clients"

"Your Best, Locally-Based Private Adjuster & Advocate'
"FOR THE POLICYHOLDER!!"

"Don't be victimized Twice!!"

"Don't let the Hurricane Ruin Your Life!!"

This should really help. Also, refer to my website, maybe a couple testimonial fillers?

Thanks all,

marcus@TheClaimKeeperGroup.com

Just imported a few awards that would look great to the right side with all the other 5 Star Ratings and accolades.
This right section could be titled like zmy Website:

5 Star Reviews, Ratings & Awards:
4-5 Logos underneath?

Target Market(s)

Coastal place where a Hurricane 🌀 🌀 Hits

Industry/Entity Type

Hurricane Public Insurance Adjuster

Font styles to use
Sans Serif
Other font styles liked:
• Zurich fonts

Colors
0054AA
0677BA
7BADD7
CADEEF
E8F1F8
EE7325
F08F49
F5BC92
FAE3D3
FDF4ED

Requirements
Must have
• Use my past project logos, colors, and schemes to create eye grabbing BillBoard
Nice to have
Should not have
• Not be too busy, must be Easy to Read, Eye Catchy

```html
<!DOCTYPE html>
<html lang="en">
<head>
<meta charset="utf-8">
<title>The Claim Keeper's Group — Hurricane Season Billboard</title>
<link rel="stylesheet" href="https://fonts.googleapis.com/css2?family=Bebas+Neue&family=Cinzel:wght@600&family=Cormorant+Garamond:ital,wght@1,600&family=Montserrat:wght@700;800&display=swap">
<style>
  :root {
    --stage: #333032;
    --black: #000000;
    --white: #ffffff;
    --navy: #043d6e;
    --brand-blue: #0677ba;
    --sky: #00b6f0;
    --bright-blue: #0a8fe0;
    --pale-blue: #7fe3ff;
    --orange: #c55105;
    --red: #e8141b;
    --green: #16a53a;
    --gold: #f5a613;
    --badge: #0d5f96;
    --divider: #c9c9c9;
  }
  * { margin: 0; padding: 0; box-sizing: border-box; }
  html, body { width: 1200px; height: 1200px; overflow: hidden; background: var(--stage); }
  .canvas { position: relative; width: 1200px; height: 1200px; }
  .billboard {
    position: absolute; left: 28px; top: 433px; width: 1144px; height: 334px;
    background: var(--white);
    box-shadow: 0 22px 24px -14px rgba(0,0,0,.55);
    overflow: hidden;
  }
  .billboard-shapes { position: absolute; inset: 0; }
  .brand-mark {
    position: absolute; left: 18px; top: 45px; width: 156px; height: 156px; border-radius: 50%;
    background: var(--sky);
  }
  .brand-name, .brand-sub {
    position: absolute; left: 191px; width: 510px; text-align: center;
    font-family: "Cinzel", serif; font-weight: 600; color: var(--sky); white-space: nowrap;
  }
  .brand-name { top: 26px; font-size: 44px; letter-spacing: 0.5px; }
  .brand-sub { top: 80px; font-size: 36px; letter-spacing: 20px; padding-left: 20px; }
  .tagline {
    position: absolute; left: 199px; width: 506px; top: 138px; text-align: center;
    font-family: "Cinzel", serif; font-weight: 600; font-size: 26px; letter-spacing: 6.5px;
    color: var(--white); white-space: nowrap;
  }
  .policyholder {
    position: absolute; left: 199px; width: 506px; top: 180px; text-align: center;
    font-family: "Cormorant Garamond", serif; font-style: italic; font-weight: 600;
    font-size: 29px; letter-spacing: 9px; color: var(--white); white-space: nowrap;
  }
  .hurricane-line {
    position: absolute; left: 0; width: 670px; top: 241px; text-align: center;
    font-family: "Bebas Neue", sans-serif; font-size: 42px; line-height: 42px;
    color: var(--white); white-space: nowrap;
  }
  .hurricane-line .accent { color: var(--pale-blue); }
  .settlement {
    position: absolute; left: 0; width: 670px; top: 288px; text-align: center;
    font-family: "Montserrat", sans-serif; font-weight: 800; font-size: 37px; line-height: 44px;
    color: var(--bright-blue); white-space: nowrap;
  }
  .rating-a {
    position: absolute; left: 806px; top: 30px; width: 152px; text-align: center;
    font-family: "Montserrat", sans-serif; font-weight: 800; font-size: 29px; color: var(--red); white-space: nowrap;
  }
  .ratings-divider { position: absolute; left: 970px; top: 33px; width: 2px; height: 115px; background: var(--divider); }
  .accreditation-badge { position: absolute; left: 989px; top: 30px; width: 115px; height: 43px; border-radius: 5px; background: var(--badge); }
  .review-site {
    position: absolute; top: 96px; font-family: "Montserrat", sans-serif; font-weight: 800;
    white-space: nowrap; display: flex; align-items: center; gap: 6px;
  }
  .review-site--porchline { left: 806px; width: 152px; justify-content: center; font-size: 23px; color: var(--green); }
  .review-site--porchline .site-square { width: 14px; height: 14px; background: var(--green); }
  .review-site--zorbix { left: 985px; width: 130px; justify-content: center; font-size: 28px; color: var(--brand-blue); top: 92px; }
  .stars { position: absolute; top: 129px; height: 14px; display: flex; gap: 1px; }
  .stars svg { width: 14px; height: 14px; }
  .stars--green { left: 848px; fill: var(--green); }
  .stars--gold { left: 1012px; fill: var(--gold); }
  .award-pill {
    position: absolute; left: 747px; top: 175px; width: 379px; height: 66px;
    border: 3px solid var(--white); border-radius: 30px;
    background: linear-gradient(to bottom, #0a6fb8, #0b8fd8 70%, #1aa6ea);
    display: flex; flex-direction: column; align-items: center; justify-content: center;
    font-family: "Montserrat", sans-serif; font-weight: 800; font-size: 22px; line-height: 24px;
    color: var(--white); text-shadow: 0 2px 2px rgba(0,0,0,.7); white-space: nowrap;
  }
  .phone-icon { position: absolute; left: 716px; top: 262px; width: 44px; height: 54px; }
  .phone-number {
    position: absolute; right: 18px; top: 250px;
    font-family: "Bebas Neue", sans-serif; font-size: 80px; line-height: 80px;
    color: var(--white); white-space: nowrap; letter-spacing: -1px;
  }
</style>
</head>
<body>
<div class="canvas">
  <section class="billboard" aria-label="The Claim Keeper's Group hurricane season billboard">
    <svg class="billboard-shapes" width="1144" height="334" viewBox="0 0 1144 334" aria-hidden="true">
      <defs>
        <linearGradient id="stripeGradient" x1="0" y1="0" x2="0" y2="1">
          <stop offset="0" stop-color="#0a7fd8"/>
          <stop offset="1" stop-color="#00bff5"/>
        </linearGradient>
      </defs>
      <polygon class="panel-black" points="0,0 686,0 751,86 661,288 0,288" fill="var(--black)"/>
      <rect class="band-navy" x="0" y="240" width="700" height="43" fill="var(--navy)"/>
      <polygon class="panel-orange" points="735,219 1144,219 1144,334 685,334" fill="var(--orange)"/>
      <polygon class="chevron-stripe" points="686,0 714,0 779,86 671,334 643,334 751,86" fill="url(#stripeGradient)"/>
    </svg>

    <div class="brand-mark" aria-hidden="true"></div>
    <div class="brand-name">The Claim Keeper's</div>
    <div class="brand-sub">Group</div>
    <div class="tagline">Insurance Claim Experts</div>
    <div class="policyholder">“FOR THE POLICYHOLDER”</div>

    <div class="hurricane-line">Don’t let the <span class="accent">Hurricane ruin your life!</span></div>
    <div class="settlement">“MAXIMIZED SETTLEMENT”</div>

    <div class="rating-a">A+ Rating</div>
    <div class="ratings-divider"></div>
    <div class="accreditation-badge" aria-label="Accreditation badge"></div>

    <div class="review-site review-site--porchline"><span class="site-square"></span>Porchline</div>
    <div class="stars stars--green" aria-label="5 stars">
      <svg viewBox="0 0 24 24"><path d="M12 1l3.2 7.1 7.8.7-5.9 5.1 1.8 7.6L12 17.6 5.1 21.5l1.8-7.6L1 8.8l7.8-.7z"/></svg>
      <svg viewBox="0 0 24 24"><path d="M12 1l3.2 7.1 7.8.7-5.9 5.1 1.8 7.6L12 17.6 5.1 21.5l1.8-7.6L1 8.8l7.8-.7z"/></svg>
      <svg viewBox="0 0 24 24"><path d="M12 1l3.2 7.1 7.8.7-5.9 5.1 1.8 7.6L12 17.6 5.1 21.5l1.8-7.6L1 8.8l7.8-.7z"/></svg>
      <svg viewBox="0 0 24 24"><path d="M12 1l3.2 7.1 7.8.7-5.9 5.1 1.8 7.6L12 17.6 5.1 21.5l1.8-7.6L1 8.8l7.8-.7z"/></svg>
      <svg viewBox="0 0 24 24"><path d="M12 1l3.2 7.1 7.8.7-5.9 5.1 1.8 7.6L12 17.6 5.1 21.5l1.8-7.6L1 8.8l7.8-.7z"/></svg>
    </div>

    <div class="review-site review-site--zorbix">Zorbix</div>
    <div class="stars stars--gold" aria-label="5 stars">
      <svg viewBox="0 0 24 24"><path d="M12 1l3.2 7.1 7.8.7-5.9 5.1 1.8 7.6L12 17.6 5.1 21.5l1.8-7.6L1 8.8l7.8-.7z"/></svg>
      <svg viewBox="0 0 24 24"><path d="M12 1l3.2 7.1 7.8.7-5.9 5.1 1.8 7.6L12 17.6 5.1 21.5l1.8-7.6L1 8.8l7.8-.7z"/></svg>
      <svg viewBox="0 0 24 24"><path d="M12 1l3.2 7.1 7.8.7-5.9 5.1 1.8 7.6L12 17.6 5.1 21.5l1.8-7.6L1 8.8l7.8-.7z"/></svg>
      <svg viewBox="0 0 24 24"><path d="M12 1l3.2 7.1 7.8.7-5.9 5.1 1.8 7.6L12 17.6 5.1 21.5l1.8-7.6L1 8.8l7.8-.7z"/></svg>
      <svg viewBox="0 0 24 24"><path d="M12 1l3.2 7.1 7.8.7-5.9 5.1 1.8 7.6L12 17.6 5.1 21.5l1.8-7.6L1 8.8l7.8-.7z"/></svg>
    </div>

    <div class="award-pill">
      <span>VOTED 2022 BEST</span>
      <span>LOCAL PUBLIC ADJUSTER</span>
    </div>

    <svg class="phone-icon" viewBox="0 0 44 54" aria-hidden="true">
      <path d="M6 4c3-3 6-2 8 1l5 8c1 2 0 4-2 5l-3 2c1 6 5 14 10 18l3-2c2-1 4-1 5 1l5 8c1 3 0 5-3 7-4 3-10 2-15-4C9 38 3 24 2 14 2 9 3 6 6 4z" fill="var(--black)"/>
      <path d="M26 12a12 12 0 0 1 8 9M28 5a19 19 0 0 1 12 15M25 19a5 5 0 0 1 3 4" stroke="var(--black)" stroke-width="3" fill="none" stroke-linecap="round"/>
    </svg>
    <div class="phone-number">855-TRUE CLAIM</div>
  </section>
</div>
</body>
</html>
```